Word Templates for Green Energy Consulting Company

Please see attached brief. This is what we'd like. Please note that we have also launched a PowerPoint template project and we want the two designs to be consistent. We encourage designers to submit to both contests. PowerPoint project is here: https://www.plumvexa.com/manage-project/brief/7381526

Font styles to use
Serif
Sans Serif

```html
<!DOCTYPE html>
<html lang="en">
<head>
<meta charset="utf-8">
<title>Kestrel Grid – Annual Report 2023 Template</title>
<link href="https://fonts.googleapis.com/css2?family=Arimo:ital,wght@0,400;0,700;1,400&family=Montserrat:wght@300;400;500;600;700&display=swap" rel="stylesheet">
<style>
:root{
  --bg:#c8c8ca;
  --navy:#1c3350;
  --blue:#1e5a8c;
  --sky:#1a86c6;
  --green:#3d9a3d;
  --green-dark:#2f7f34;
  --grey-box:#efeff1;
  --text:#3a3a3a;
  --white:#ffffff;
}
*{margin:0;padding:0;box-sizing:border-box}
html,body{width:1200px;height:2422px;overflow:hidden;background:var(--bg)}
body{position:relative;font-family:"Montserrat",sans-serif;color:var(--text)}

.cover{position:absolute;left:362px;top:93px;width:484px;height:686px;background:var(--white);overflow:hidden}
.cover-art{position:absolute;inset:0}
.cover-title{position:absolute;left:31px;top:28px;font-family:"Montserrat",sans-serif;font-weight:500;font-size:54px;line-height:60px;color:#e8ecf0;letter-spacing:1px}
.cover-title .year{display:block;color:var(--green);font-weight:700}
.brand-block{position:absolute;left:0;right:0;top:530px;text-align:center}
.brand-name{display:inline-flex;align-items:center;gap:12px;font-family:"Montserrat",sans-serif;font-weight:700;font-size:36px;color:var(--navy)}
.brand-square{width:26px;height:26px;background:var(--green)}
.brand-tagline{display:flex;align-items:center;justify-content:center;gap:10px;margin-top:10px;font-size:16px;color:var(--green-dark)}
.brand-tagline::before,.brand-tagline::after{content:"";width:58px;height:2px;background:var(--green-dark)}
.cover-web{position:absolute;left:0;right:0;top:645px;text-align:center;font-size:11px;letter-spacing:5px;color:#333}

.page{position:absolute;width:485px;height:686px;background:var(--white);overflow:hidden}
.page-tl{left:87px;top:870px}
.page-tr{left:639px;top:870px}
.page-bl{left:87px;top:1619px}
.page-br{left:639px;top:1619px}

.page-header{position:absolute;left:0;top:0;width:100%;height:27px;background:linear-gradient(90deg,var(--navy),var(--blue) 60%,var(--sky))}
.page-header::after{content:"";position:absolute;left:85px;right:0;bottom:0;height:5px;background:var(--green);clip-path:polygon(0 100%,6px 0,100% 0,100% 100%)}
.page-header span{position:absolute;right:18px;top:8px;font-size:7.5px;letter-spacing:3.2px;color:var(--white)}

.page-footer{position:absolute;left:0;top:651px;width:100%;height:17px}
.footer-brand{position:absolute;left:22px;top:0;display:flex;align-items:center;gap:6px;font-weight:700;font-size:11px;color:var(--navy)}
.footer-brand .brand-square{width:11px;height:11px}
.footer-bar{position:absolute;left:170px;right:0;top:0;height:17px;background:var(--green);clip-path:polygon(0 0,100% 0,100% 100%,6px 100%)}
.page-num{position:absolute;right:14px;top:4px;font-size:6px;font-weight:700;color:var(--white)}

.content{position:absolute;left:19px;right:20px;top:44px}
.section-title{font-family:"Arimo",sans-serif;font-weight:700;font-size:15.5px;color:var(--green);line-height:18px}
.section-sub{font-family:"Arimo",sans-serif;font-size:10.5px;color:var(--blue);margin:2px 0 9px}
.section-sub.strong{font-weight:700}
.body-copy{font-size:7.2px;line-height:15.6px;text-align:justify;margin-bottom:15px}
.section{margin-bottom:4px}
.sub-heading{font-family:"Arimo",sans-serif;font-style:italic;font-weight:400;font-size:9.5px;color:var(--blue);margin:2px 0 2px}

.toc-title{position:absolute;left:25px;top:44px;font-family:"Arimo",sans-serif;font-weight:700;font-size:15.5px;line-height:18px;color:var(--green)}
.toc-title span{color:var(--blue);display:block;margin-top:6px}
.toc-row{position:absolute;left:23px;width:436px;height:58px}
.toc-entry{position:absolute;left:0;top:0;width:350px;height:58px;background:var(--grey-box);border-left:3px solid var(--green);clip-path:polygon(0 0,332px 0,350px 100%,0 100%);padding:7px 30px 0 11px}
.toc-entry h3{font-family:"Arimo",sans-serif;font-weight:700;font-size:11px;color:var(--blue);margin-bottom:2px}
.toc-entry p{font-size:6.3px;line-height:9.4px}
.toc-num{position:absolute;left:329px;top:0;width:107px;height:58px;border-top:3px solid var(--grey-box);clip-path:polygon(0 0,100% 0,100% 100%,20px 100%)}
.toc-num span{position:absolute;left:44px;top:19px;font-weight:600;font-size:14px;color:var(--green)}

.split{display:flex;gap:14px}
.split .col{width:246px}
.photo-slot{width:186px;height:211px;margin-top:-4px;background:linear-gradient(160deg,#dfe9f3,#b7c8d6 55%,#8c9a86)}
</style>
</head>
<body>

<section class="cover">
  <svg class="cover-art" width="484" height="686" viewBox="0 0 484 686">
    <defs>
      <linearGradient id="coverSky" x1="0" y1="0" x2="1" y2="0.4">
        <stop offset="0" stop-color="#1d4a73"/>
        <stop offset="0.6" stop-color="#1f5f8f"/>
        <stop offset="1" stop-color="#1b86c4"/>
      </linearGradient>
    </defs>
    <polygon points="0,0 484,0 484,294 0,382" fill="url(#coverSky)" role="img" aria-label="Photo of hands holding light bulbs under a blue tint"/>
    <polygon points="0,382 484,294 484,303 0,391" fill="#3d9a3d"/>
  </svg>
  <h1 class="cover-title">ANNUAL<br>REPORT<span class="year">2023</span></h1>
  <div class="brand-block">
    <div class="brand-name"><span class="brand-square"></span>Kestrel Grid</div>
    <div class="brand-tagline">Clear Energy, Smart Choices</div>
  </div>
  <div class="cover-web">www.kestrelgrid.com</div>
</section>

<section class="page page-tl">
  <header class="page-header"><span>CLEAR ENERGY, SMART CHOICES</span></header>
  <h2 class="toc-title">TABLE<span>OF CONTENT</span></h2>
  <div class="toc-row" style="top:96px"><div class="toc-entry"><h3>HEADING GOES HERE</h3><p>Lorem ipsum dolor sit amet, consectetuer adipiscing elit, sed diam nonummy nibh euismod tincidunt ut. Lorem ipsum dolor sit amet, consectetuer adipiscing elit, sed diam nonummy nibh euismod tincidunt ut</p></div><div class="toc-num"><span>01</span></div></div>
  <div class="toc-row" style="top:165px"><div class="toc-entry"><h3>HEADING GOES HERE</h3><p>Lorem ipsum dolor sit amet, consectetuer adipiscing elit, sed diam nonummy nibh euismod tincidunt ut. Lorem ipsum dolor sit amet, consectetuer adipiscing elit, sed diam nonummy nibh euismod tincidunt ut</p></div><div class="toc-num"><span>02</span></div></div>
  <div class="toc-row" style="top:235px"><div class="toc-entry"><h3>HEADING GOES HERE</h3><p>Lorem ipsum dolor sit amet, consectetuer adipiscing elit, sed diam nonummy nibh euismod tincidunt ut. Lorem ipsum dolor sit amet, consectetuer adipiscing elit, sed diam nonummy nibh euismod tincidunt ut</p></div><div class="toc-num"><span>03</span></div></div>
  <div class="toc-row" style="top:304px"><div class="toc-entry"><h3>HEADING GOES HERE</h3><p>Lorem ipsum dolor sit amet, consectetuer adipiscing elit, sed diam nonummy nibh euismod tincidunt ut. Lorem ipsum dolor sit amet, consectetuer adipiscing elit, sed diam nonummy nibh euismod tincidunt ut</p></div><div class="toc-num"><span>04</span></div></div>
  <div class="toc-row" style="top:374px"><div class="toc-entry"><h3>HEADING GOES HERE</h3><p>Lorem ipsum dolor sit amet, consectetuer adipiscing elit, sed diam nonummy nibh euismod tincidunt ut. Lorem ipsum dolor sit amet, consectetuer adipiscing elit, sed diam nonummy nibh euismod tincidunt ut</p></div><div class="toc-num"><span>05</span></div></div>
  <div class="toc-row" style="top:443px"><div class="toc-entry"><h3>HEADING GOES HERE</h3><p>Lorem ipsum dolor sit amet, consectetuer adipiscing elit, sed diam nonummy nibh euismod tincidunt ut. Lorem ipsum dolor sit amet, consectetuer adipiscing elit, sed diam nonummy nibh euismod tincidunt ut</p></div><div class="toc-num"><span>06</span></div></div>
  <footer class="page-footer"><div class="footer-brand"><span class="brand-square"></span>Kestrel Grid</div><div class="footer-bar"></div></footer>
</section>

<section class="page page-tr">
  <header class="page-header"><span>CLEAR ENERGY, SMART CHOICES</span></header>
  <div class="content">
    <div class="section">
      <h2 class="section-title">HEADING GOES HERE</h2>
      <p class="section-sub">SUBTITLE GOES HERE</p>
      <p class="body-copy">Lorem ipsum dolor sit amet, consectetuer adipiscing elit, sed diam nonummy nibh euismod tincidunt ut laoreet dolore magna aliquam erat volutpat. Ut wisi enim ad minim veniam, quis nostrud exerci tation ullamcorper suscipit lobortis nisl ut aliquip ex ea commodo consequat. Duis autem vel eum iriure dolor in hendrerit in vulputate velit esse molestie consequat, vel illum dolore eu feugiat nulla facilisis at vero eros et accumsan et iusto odio dignissim qui blandit praesent luptatum zzril delenit augue duis dolore te feugait nulla facilisi.</p>
      <p class="body-copy">Lorem ipsum dolor sit amet, cons ectetuer adipiscing elit, sed diam nonummy nibh euismod tincidunt ut laoreet dolore magna aliquam erat volutpat. Ut wisi enim ad minim veniam, quis nostrud exerci tation ullamcorper suscipit lobortis nisl ut aliquip ex ea commodo consequat.</p>
    </div>
    <div class="section">
      <h2 class="section-title">HEADING GOES HERE</h2>
      <p class="section-sub">SUBTITLE GOES HERE</p>
      <p class="body-copy">Lorem ipsum dolor sit amet, consectetuer adipiscing elit, sed diam nonummy nibh euismod tincidunt ut laoreet dolore magna aliquam erat volutpat. Ut wisi enim ad minim veniam, quis nostrud exerci tation ullamcorper suscipit lobortis nisl ut aliquip ex ea commodo consequat. Duis autem vel eum iriure dolor in hendrerit in vulputate velit esse molestie consequat, vel illum dolore eu feugiat nulla facilisis at vero eros et accumsan et iusto odio dignissim qui blandit praesent luptatum zzril delenit augue duis dolore te feugait nulla facilisi.</p>
      <p class="body-copy">Lorem ipsum dolor sit amet, cons ectetuer adipiscing elit, sed diam nonummy nibh euismod tincidunt ut laoreet dolore magna aliquam erat volutpat. Ut wisi enim ad minim veniam, quis nostrud exerci tation ullamcorper suscipit lobortis nisl ut aliquip ex ea commodo consequat.</p>
    </div>
    <div class="section">
      <h2 class="section-title">HEADING GOES HERE</h2>
      <p class="section-sub">SUBTITLE GOES HERE</p>
      <p class="body-copy">Lorem ipsum dolor sit amet, consectetuer adipiscing elit, sed diam nonummy nibh euismod tincidunt ut laoreet dolore magna aliquam erat volutpat. Ut wisi enim ad minim veniam, quis nostrud exerci tation ullamcorper suscipit lobortis nisl ut aliquip ex ea commodo consequat. Duis autem vel eum iriure dolor in hendrerit in vulputate velit esse molestie consequat, vel illum dolore eu feugiat nulla facilisis at vero eros et accumsan et iusto odio dignissim qui blandit praesent luptatum zzril delenit augue duis dolore te feugait nulla facilisi.</p>
      <p class="body-copy">Lorem ipsum dolor sit amet, cons ectetuer adipiscing elit, sed diam nonummy nibh euismod tincidunt ut laoreet dolore magna aliquam erat volutpat. Ut wisi enim ad minim veniam, quis nostrud exerci tation ullamcorper suscipit lobortis nisl ut aliquip ex ea commodo consequat.</p>
    </div>
  </div>
  <footer class="page-footer"><div class="footer-brand"><span class="brand-square"></span>Kestrel Grid</div><div class="footer-bar"><span class="page-num">PAGE | 01</span></div></footer>
</section>

<section class="page page-bl">
  <header class="page-header"><span>CLEAR ENERGY, SMART CHOICES</span></header>
  <div class="content">
    <div class="section">
      <h2 class="section-title">HEADING GOES HERE</h2>
      <p class="section-sub">SUBTITLE GOES HERE</p>
      <p class="body-copy">Lorem ipsum dolor sit amet, consectetuer adipiscing elit, sed diam nonummy nibh euismod tincidunt ut laoreet dolore magna aliquam erat volutpat. Ut wisi enim ad minim veniam, quis nostrud exerci tation ullamcorper suscipit lobortis nisl ut aliquip ex ea commodo consequat. Duis autem vel eum iriure dolor in hendrerit in vulputate velit esse molestie consequat, vel illum dolore eu feugiat nulla facilisis at vero eros et accumsan et iusto odio dignissim qui blandit praesent luptatum zzril delenit augue duis dolore te feugait nulla facilisi.</p>
      <p class="body-copy">Lorem ipsum dolor sit amet, cons ectetuer adipiscing elit, sed diam nonummy nibh euismod tincidunt ut laoreet dolore magna aliquam erat volutpat. Ut wisi enim ad minim veniam, quis nostrud exerci tation ullamcorper suscipit lobortis nisl ut aliquip ex ea commodo consequat.</p>
      <p class="body-copy">Lorem ipsum dolor sit amet, consectetuer adipiscing elit, sed diam nonummy nibh euismod tincidunt ut laoreet dolore magna aliquam erat volutpat. Ut wisi enim ad minim veniam, quis nostrud exerci tation ullamcorper suscipit lobortis nisl ut aliquip ex ea commodo consequat. Duis autem vel eum iriure dolor in hendrerit in vulputate velit esse molestie consequat, vel illum dolore eu feugiat nulla facilisis at vero eros et accumsan et iusto odio dignissim qui blandit praesent luptatum zzril delenit augue duis dolore te feugait nulla facilisi.</p>
    </div>
    <div class="section">
      <h2 class="section-title">HEADING GOES HERE</h2>
      <p class="section-sub">SUBTITLE GOES HERE</p>
      <div class="split">
        <div class="col">
          <p class="body-copy">Lorem ipsum dolor sit amet, consectetuer adipiscing elit, sed diam nonummy nibh euismod tincidunt ut laoreet dolore magna aliquam erat volutpat. Ut wisi enim ad minim veniam, quis nostrud exerci tation ullamcorper suscipit lobortis nisl ut aliquip ex ea commodo consequat. Duis autem vel eum iriure dolor in hendrerit in vulputate velit esse molestie consequat, vel illum dolore eu feugiat nulla facilisis at vero eros et accumsan et iusto odio dignissim qui blandit praesent luptatum zzril delenit augue duis dolore te feugait nulla facilisi.</p>
          <p class="body-copy">Lorem ipsum dolor sit amet, cons ectetuer adipiscing elit, sed diam nonummy nibh euismod tincidunt ut laoreet dolore magna aliquam erat volutpat. Ut wisi enim ad minim veniam, quis nostrud exerci tation ullamcorper suscipit lobortis nisl ut aliquip ex ea commodo consequat.</p>
        </div>
        <div class="photo-slot" role="img" aria-label="Photo of several hands raising light bulbs against a bright sky"></div>
      </div>
    </div>
  </div>
  <footer class="page-footer"><div class="footer-brand"><span class="brand-square"></span>Kestrel Grid</div><div class="footer-bar"><span class="page-num">PAGE | 02</span></div></footer>
</section>

<section class="page page-br">
  <header class="page-header"><span>CLEAR ENERGY, SMART CHOICES</span></header>
  <div class="content">
    <h2 class="section-title">HEADING GOES HERE</h2>
    <p class="section-sub strong">SUBTITLE GOES HERE</p>
    <h3 class="sub-heading">"1." Heading 1</h3>
    <p class="body-copy">Lorem ipsum dolor sit amet, consectetuer adipiscing elit, sed diam nonummy nibh euismod tincidunt ut laoreet dolore magna aliquam erat volutpat. Ut wisi enim ad minim veniam, quis nostrud exerci tation ullamcorper suscipit lobortis nisl ut aliquip ex ea commodo consequat. Duis autem vel eum iriure dolor in hendrerit in vulputate velit esse molestie consequat, vel illum dolore eu feugiat nulla facilisis at vero eros et accumsan et iusto odio dignissim qui blandit praesent luptatum zzril delenit augue duis dolore te feugait nulla facilisi.</p>
    <h3 class="sub-heading">"1.1. Heading 2</h3>
    <p class="body-copy">Lorem ipsum dolor sit amet, consectetuer adipiscing elit, sed diam nonummy nibh euismod tincidunt ut laoreet dolore magna aliquam erat volutpat. Ut wisi enim ad minim veniam, quis nostrud exerci tation ullamcorper suscipit lobortis nisl ut aliquip ex ea commodo consequat. Duis autem vel eum iriure dolor in hendrerit in vulputate velit esse molestie consequat, vel illum dolore eu feugiat nulla facilisis at vero eros et accumsan et iusto odio dignissim qui blandit praesent luptatum zzril delenit augue duis dolore te feugait nulla facilisi.</p>
    <h3 class="sub-heading">"1.1.1. Heading 3</h3>
    <p class="body-copy">Lorem ipsum dolor sit amet, consectetuer adipiscing elit, sed diam nonummy nibh euismod tincidunt ut laoreet dolore magna aliquam erat volutpat. Ut wisi enim ad minim veniam, quis nostrud exerci tation ullamcorper suscipit lobortis nisl ut aliquip ex ea commodo consequat. Duis autem vel eum iriure dolor in hendrerit in vulputate velit esse molestie consequat, vel illum dolore eu feugiat nulla facilisis at vero eros et accumsan et iusto odio dignissim qui blandit praesent luptatum zzril delenit augue duis dolore te feugait nulla facilisi.</p>
  </div>
  <footer class="page-footer"><div class="footer-brand"><span class="brand-square"></span>Kestrel Grid</div><div class="footer-bar"><span class="page-num">PAGE | 03</span></div></footer>
</section>

</body>
</html>
```